Meal Plan Website Needs New Pages Designed

Brightwick Supper Kits is an online, membership based program that delivers weekly meal programs (7 days worth of recipes plus shopping lists) carefully crafted by an expert team of meal planners. All recipes are created to comply with the following macronutrient ratio: 65% healthy fats, 25% lean protein, 10% good carbs.
All recipes are Paleo friendly and a great resource for those individuals who want to correctly implement this type of diet.

We are re-designing our website and need the following pages designed:

· Home page w/ logo
· How it works page
· Get Started! page
· Recipes Page template (these will be the pages on our site that will have recipes)
· Kitchen Essentials Training page (this will be a page with videos and tips + tricks, PDFs, etc)

So 5 total PSDs, 1 for each page.

Target audience: Men and women between the ages of 30 and 60 who want to:
· Eat healthy
· Lose weight
· Follow/Implement the Paleo diet
· Take the guesswork out of preparing delicious AND healthy meals for them and their families
· Know exactly what to eat, what to buy, how to make it

Feelings/Messages we want to communicate through the design:
· “Organic” but elegant look
· Fresh/light/Airy
· Simple but NOT GENERIC
· “I want to get cooking” feeling

Our Stylistic preferences:
· Minimalist with a few bold elements (something in between)
· Easy to visually navigate (enough white space, but not too much)
· There is more to “see” than to “read”

Our Color Preferences:
· Lighter pallet
· Colors that evoke natural woods, granite countertops…
· Stay away from using all dark colors

Our Font Type Preferences:
· Easy to read
· Not more than 3 font types
· Not too rigid
· Not too sophisticated
· Simple with a touch

Examples of Website Designs that we like:
· http://www.dorvanta.com/meal-plans/
· http://grulvix.com/
· https://www.mistobarn.com/

```html
<!DOCTYPE html>
<html lang="en">
<head>
<meta charset="utf-8">
<title>Brightwick Supper Kits</title>
<link rel="stylesheet" href="https://fonts.googleapis.com/css2?family=Open+Sans:ital,wght@0,300;0,400;0,600;0,700;1,400&display=swap">
<style>
:root{
  --green:#8db220;
  --green-band:#a6c532;
  --green-card:#98b82b;
  --green-btn:#93b82a;
  --text:#5a5a5a;
  --muted:#8a8a8a;
  --cream:#f7f6ef;
  --card-border:#e6e4d6;
  --icon:#dcd8c6;
  --footer:#f4f4f2;
  --dark:#3c3c3c;
}
*{margin:0;padding:0;box-sizing:border-box}
html,body{width:1200px;height:2326px;overflow:hidden;background:#fff}
body{position:relative;font-family:"Open Sans",Arial,sans-serif;color:var(--text)}
.abs{position:absolute}

/* header */
.site-header{left:0;top:0;width:1200px;height:104px;background:#fff}
.brand{left:132px;top:36px;display:flex;align-items:center;gap:10px}
.brand-dot{width:30px;height:30px;border-radius:50%;background:var(--green)}
.brand-name{font-size:24px;font-weight:400;color:var(--green);letter-spacing:.2px}
.main-nav{left:502px;top:46px;display:flex;gap:0}
.main-nav a{font-size:16px;color:#6b6b6b;text-decoration:none;margin-right:36px}
.main-nav a.active{color:var(--green);font-weight:600}

/* hero */
.hero{left:0;top:104px;width:1200px;height:507px;
  background:radial-gradient(ellipse at 50% 40%,#6b655c 0%,#2e2a26 45%,#141210 100%)}
.hero-dots{left:584px;top:582px;display:flex;gap:8px}
.hero-dots span{width:13px;height:13px;border-radius:50%;background:#fff}

/* features */
.feature{top:648px;width:284px;height:294px;border:1px solid var(--card-border);
  background:linear-gradient(#fff 70%,#f6f5ee);text-align:center}
.feature svg{display:block;margin:40px auto 0}
.feature h3{font-size:24px;font-weight:400;color:var(--green);margin-top:22px}
.feature p{font-size:12.5px;line-height:20px;color:var(--muted);padding:4px 22px 0}

/* what we do */
.about{left:0;top:987px;width:1200px;height:380px;background:var(--cream)}
.about h2{left:135px;top:64px;font-size:35px;font-weight:300;color:var(--green)}
.about .lead{left:136px;top:118px;width:500px;font-size:15.5px;line-height:24px;color:#7a7a6e}
.about .body{left:136px;top:167px;width:500px;font-size:12.5px;line-height:20px;color:var(--muted)}
.btn{left:134px;top:271px;width:137px;height:34px;background:linear-gradient(#a3c73a,#86ab1d);
  color:#fff;font-size:15px;font-weight:600;text-align:center;line-height:34px;border-radius:2px}
.about .dish{left:655px;top:60px;width:390px;height:240px;border-radius:12px;transform:rotate(-8deg);
  background:radial-gradient(ellipse at 45% 55%,#a25c2a 0%,#c9a24a 30%,#7fa640 50%,#f2f0ea 72%,#f7f6ef 100%)}

/* recipes */
.recipes{left:0;top:1367px;width:1200px;height:430px;background:var(--green-band)}
.recipes h2{left:0;width:1200px;top:44px;text-align:center;font-size:36px;font-weight:300;color:#fff}
.recipe{top:112px;width:229px;height:257px;background:var(--green-card)}
.recipe .photo{height:139px}
.recipe h4{font-size:16px;font-weight:400;color:#fff;margin:11px 0 0 21px;letter-spacing:.3px}
.recipe p{font-size:11.5px;line-height:18px;color:#f2f7de;margin:3px 16px 0 21px}

/* testimonials */
.testimonials-title{left:0;width:1200px;top:1842px;text-align:center;font-size:34px;font-weight:300;color:var(--dark)}
.quote-card{top:1914px;width:400px;height:210px;background:var(--cream);border:1px solid #ebe9dc}
.avatar{left:22px;top:26px;width:80px;height:80px;border-radius:50%;background:radial-gradient(circle,#d9b79a,#8a6a52)}
.quote-card blockquote{left:116px;top:18px;width:262px;font-size:11.2px;line-height:21.5px;font-style:italic;color:#8a8a7e}
.quote-card cite{left:116px;top:162px;font-style:normal;font-size:13px;font-weight:600;color:#555}

/* footer */
.site-footer{left:0;top:2201px;width:1200px;height:125px;background:var(--footer);border-top:1px solid #e8e8e8}
.footer-nav{left:135px;top:34px;font-size:15px;color:#444}
.footer-nav span{color:#777;margin:0 7px}
.copyright{left:135px;top:70px;font-size:11.5px;color:#777}
.social{top:34px;width:24px;height:24px;border-radius:2px}
</style>
</head>
<body>

<header class="site-header abs">
  <div class="brand abs"><span class="brand-dot"></span><span class="brand-name">Brightwick Supper Kits</span></div>
  <nav class="main-nav abs">
    <a class="active" href="#">Home</a><a href="#">About Us</a><a href="#">Recipes</a><a href="#">Resource</a><a href="#">Testimonials</a><a href="#">Contact</a>
  </nav>
</header>

<section class="hero abs" role="img" aria-label="Chef in white uniform standing at a carving station with heat lamps and a buffet of roasted meats"></section>
<div class="hero-dots abs"><span></span><span></span><span></span></div>

<article class="feature abs" style="left:152px">
  <svg width="96" height="90" viewBox="0 0 96 90"><rect x="38" y="4" width="20" height="8" rx="3" fill="var(--icon)"/><path d="M8 70 A40 40 0 0 1 88 70 Z" fill="var(--icon)"/><rect x="2" y="74" width="92" height="8" rx="3" fill="var(--icon)"/></svg>
  <h3>Meal Plans</h3>
  <p>Etiam eu urna Sed porta Suspendisse quam leo molestie sed luctus quis feugiat in pede Fusce tellus Sed</p>
</article>
<article class="feature abs" style="left:460px">
  <svg width="96" height="90" viewBox="0 0 96 90"><rect x="22" y="4" width="56" height="80" rx="4" fill="none" stroke="var(--icon)" stroke-width="4"/><line x1="34" y1="6" x2="34" y2="82" stroke="var(--icon)" stroke-width="4"/><line x1="46" y1="24" x2="66" y2="24" stroke="var(--icon)" stroke-width="4"/><line x1="46" y1="36" x2="66" y2="36" stroke="var(--icon)" stroke-width="4"/></svg>
  <h3>Quick Start Guide</h3>
  <p>Etiam eu urna Sed porta Suspendisse quam leo molestie sed luctus quis feugiat in pede Fusce tellus Sed</p>
</article>
<article class="feature abs" style="left:770px">
  <svg width="96" height="90" viewBox="0 0 96 90"><circle cx="48" cy="20" r="14" fill="none" stroke="var(--icon)" stroke-width="4"/><path d="M20 84 V50 Q20 38 34 38 H62 Q76 38 76 50 V84" fill="none" stroke="var(--icon)" stroke-width="4"/><rect x="30" y="48" width="36" height="30" fill="none" stroke="var(--icon)" stroke-width="4"/></svg>
  <h3>At home workouts</h3>
  <p>Etiam eu urna Sed porta Suspendisse quam leo molestie sed luctus quis feugiat in pede Fusce tellus Sed</p>
</article>

<section class="about abs">
  <h2 class="abs">What We Do</h2>
  <p class="lead abs">Etiam eu urna Sed porta Suspendisse quam leo molestie sed luctus quis feugiat in pede Fusce tellus</p>
  <p class="body abs">eu ante Integer orci tellus tristique vitae consequat nec porta vel lectus Nulla sit amet diam Duis non nunc libero a tempus libero lectus feugiat felis Morbi diam mauris viverra in gravida eu mattis in ante Morbi eget arcu Morbi porta libero id ullamcorper nonummy nibh ligula pulvinar metus</p>
  <div class="btn abs">Read More</div>
  <div class="dish abs" role="img" aria-label="Grilled steak with roasted potatoes and fresh salad on a white plate"></div>
</section>

<section class="recipes abs">
  <h2 class="abs">Latest Meals &amp; Recipes</h2>
  <article class="recipe abs" style="left:132px"><div class="photo" role="img" aria-label="Grilled salmon with green beans and lemon" style="background:linear-gradient(135deg,#f4ece0,#e8905a 45%,#8aa04a 75%,#f0efe8)"></div><h4>MEAL RECIPE TITTLE</h4><p>Mauris nunc quam venenatis nec euismod sit amet egestas placerat est Pellentesque habitant</p></article>
  <article class="recipe abs" style="left:367px"><div class="photo" role="img" aria-label="Pasta salad with vegetables and herbs" style="background:linear-gradient(135deg,#eef0f2,#e0b070 45%,#d8763a 70%,#f3f3f3)"></div><h4>MEAL RECIPE TITTLE</h4><p>Mauris nunc quam venenatis nec euismod sit amet egestas placerat est Pellentesque habitant</p></article>
  <article class="recipe abs" style="left:603px"><div class="photo" role="img" aria-label="Glazed grilled meat with green beans and salad" style="background:linear-gradient(135deg,#6e9a36,#8a3a22 45%,#5d2414 65%,#9cc04a)"></div><h4>MEAL RECIPE TITTLE</h4><p>Mauris nunc quam venenatis nec euismod sit amet egestas placerat est Pellentesque habitant</p></article>
  <article class="recipe abs" style="left:839px"><div class="photo" role="img" aria-label="Sliced roast meat with salad greens" style="background:linear-gradient(135deg,#e8e6e0,#a87868 45%,#7a8a4a 70%,#ecebe6)"></div><h4>MEAL RECIPE TITTLE</h4><p>Mauris nunc quam venenatis nec euismod sit amet egestas placerat est Pellentesque habitant</p></article>
</section>

<h2 class="testimonials-title abs">Customer Testimonials</h2>
<figure class="quote-card abs" style="left:183px">
  <div class="avatar abs" role="img" aria-label="Customer portrait"></div>
  <blockquote class="abs">Etiam est nunc venenatis in tristique eu imperdiet ac nisl Cum sociis natoque penatibus et magnis dis parturient montes nascetur ridiculus mus In iaculis facilisis massa Etiam eu urna Sed porta Suspendisse quam leo molestie sed luctus quis feugiat in pede Fusce tellus Sed metus augue convallis</blockquote>
  <cite class="abs">By Author Name</cite>
</figure>
<figure class="quote-card abs" style="left:618px">
  <div class="avatar abs" role="img" aria-label="Customer portrait"></div>
  <blockquote class="abs">Etiam est nunc venenatis in tristique eu imperdiet ac nisl Cum sociis natoque penatibus et magnis dis parturient montes nascetur ridiculus mus In iaculis facilisis massa Etiam eu urna Sed porta Suspendisse quam leo molestie sed luctus quis feugiat in pede Fusce tellus Sed metus augue convallis</blockquote>
  <cite class="abs">By Author Name</cite>
</figure>

<footer class="site-footer abs">
  <nav class="footer-nav abs">Home<span>|</span>About Us<span>|</span>Recipes<span>|</span>Resource<span>|</span>Testimonials<span>|</span>Contact</nav>
  <p class="copyright abs">© 2014 Company Name &nbsp;All right reserved &nbsp;Term of Use</p>
  <span class="social abs" style="left:933px;background:#3b5a9a"></span>
  <span class="social abs" style="left:969px;background:#4cb4e6"></span>
  <span class="social abs" style="left:1004px;background:#1f6fa8"></span>
  <span class="social abs" style="left:1037px;background:#f08a1c"></span>
</footer>

</body>
</html>
```